Birchline Septic Solutions

Would like to see some single sided ones but would also like to see some double sided with one sided only being the logo. Owners name is Colin Vandro. Phone number is 555-214-0387
Services are pumping, inspections, installs, and repairs

Contact Information for Business Card

555-241-0387 Colin Vandro Ashford Ridge, OH

```html
<!DOCTYPE html>
<html lang="en">
<head>
<meta charset="utf-8">
<title>Birchline Septic Solutions – Business Cards</title>
<link href="https://fonts.googleapis.com/css2?family=Montserrat:wght@500;700;800&display=swap" rel="stylesheet">
<style>
  :root {
    --backdrop: #e8e8e6;
    --card: #2c2c2c;
    --teal: #2bb8b1;
    --white: #ffffff;
    --soft: #d9d9d9;
    --scene-top: #ffffff;
    --scene-bottom: #e2e2e2;
  }
  * { margin: 0; padding: 0; box-sizing: border-box; }
  html, body { width: 1200px; height: 802px; overflow: hidden; }
  body {
    background: var(--backdrop);
    font-family: "Montserrat", Arial, sans-serif;
    display: flex;
    align-items: center;
    justify-content: center;
    gap: 40px;
  }
  .card {
    position: relative;
    width: 540px;
    height: 309px;
    background: var(--card);
    border-bottom: 4px solid var(--teal);
    overflow: hidden;
  }

  /* Front side */
  .corner-tab {
    position: absolute;
    top: 0; right: 22px;
    width: 14px; height: 26px;
    background: var(--teal);
  }
  .owner {
    position: absolute;
    top: 24px; right: 46px;
    text-align: right;
  }
  .owner-name {
    color: var(--teal);
    font-weight: 700;
    font-size: 20px;
    letter-spacing: 0.5px;
    text-transform: uppercase;
  }
  .owner-role {
    color: var(--white);
    font-weight: 500;
    font-size: 12px;
    margin-top: 2px;
  }
  .scene-area {
    position: absolute;
    right: 0; bottom: 0;
    width: 230px; height: 215px;
    background: linear-gradient(180deg, var(--scene-top), var(--scene-bottom));
  }
  .wordmark {
    color: var(--white);
    font-weight: 800;
    text-transform: uppercase;
    line-height: 1.05;
  }
  .wordmark .line-main { display: block; }
  .wordmark .line-sub { display: block; }
  .front .wordmark {
    position: absolute;
    left: 34px; top: 104px;
  }
  .front .wordmark .line-main { font-size: 40px; letter-spacing: 1px; }
  .front .wordmark .line-sub { font-size: 12px; margin-top: 4px; letter-spacing: 4px; }
  .contact {
    position: absolute;
    left: 34px; bottom: 40px;
    color: var(--white);
  }
  .contact-city { font-size: 13px; font-weight: 500; color: var(--soft); }
  .contact-phone {
    display: flex; align-items: center; gap: 6px;
    font-size: 15px; font-weight: 700; margin-top: 6px;
  }
  .contact-phone svg { width: 13px; height: 13px; }

  /* Back side */
  .back {
    display: flex;
    align-items: center;
    justify-content: center;
  }
  .back .wordmark { text-align: center; }
  .back .wordmark .line-main { font-size: 50px; letter-spacing: 1px; }
  .back .wordmark .line-sub { font-size: 14px; margin-top: 8px; letter-spacing: 6px; }
</style>
</head>
<body>

  <section class="card front" aria-label="Business card front">
    <div class="scene-area" role="img" aria-label="Illustration of mountain peaks above a row of pine trees"></div>
    <div class="corner-tab"></div>
    <div class="owner">
      <p class="owner-name">Colin Vandro</p>
      <p class="owner-role">Owners</p>
    </div>

    <p class="wordmark">
      <span class="line-main">Birchline</span>
      <span class="line-sub">Septic Solutions</span>
    </p>

    <div class="contact">
      <p class="contact-city">Ashford Ridge, OH</p>
      <p class="contact-phone">
        <svg viewBox="0 0 24 24" aria-hidden="true"><circle cx="12" cy="12" r="11" fill="var(--teal)"/><path d="M8 6.5l2 2-1.2 1.6a8 8 0 0 0 5.1 5.1l1.6-1.2 2 2-1.3 1.8c-4.8-.5-9.3-5-9.8-9.8z" fill="var(--card)"/></svg>
        555-214-0387
      </p>
    </div>
  </section>

  <section class="card back" aria-label="Business card back">
    <p class="wordmark">
      <span class="line-main">Birchline</span>
      <span class="line-sub">Septic Solutions</span>
    </p>
  </section>

</body>
</html>
```